Business Card Design Project

Business card based on attached logo

Todd Merrick
Todd@lorvantest.com
877-514-9073 ext. 318
Www.LorvanTest.com

Industry/Entity Type

Business

```html
<!DOCTYPE html>
<html lang="en">
<head>
<meta charset="utf-8">
<title>LorvanTest Business Cards</title>
<link rel="stylesheet" href="https://fonts.googleapis.com/css2?family=Roboto+Condensed:wght@400;700&family=Source+Sans+3:wght@400&display=swap">
<style>
  :root {
    --backdrop: #e9e6e2;
    --card-white: #ffffff;
    --brand-red: #e41e26;
    --deep-red: #b01c24;
    --ink: #111111;
    --text-grey: #333333;
    --label-ink: #1a1a1a;
    --tint: #fbe6df;
    --panel-grey-top: #f2f2f2;
    --panel-grey-bottom: #e2e2e2;
  }
  html, body {
    margin: 0;
    padding: 0;
    width: 1200px;
    height: 788px;
    overflow: hidden;
    background: var(--backdrop);
  }
  .sheet {
    position: relative;
    width: 1200px;
    height: 788px;
    font-family: "Roboto Condensed", Arial, sans-serif;
  }
  .side-label {
    position: absolute;
    width: 526px;
    text-align: center;
    font-family: "Source Sans 3", Arial, sans-serif;
    font-size: 22px;
    color: var(--label-ink);
  }
  .card {
    position: absolute;
    width: 526px;
    height: 300px;
    border-radius: 22px;
    overflow: hidden;
    background: var(--card-white);
  }
  .card--red { background: linear-gradient(180deg, var(--brand-red) 0%, var(--deep-red) 100%); }
  .card--grey { background: linear-gradient(180deg, var(--panel-grey-top) 0%, var(--panel-grey-bottom) 100%); }

  .brand-name {
    position: absolute;
    left: 0;
    width: 100%;
    text-align: center;
    font-family: "Roboto Condensed", Arial, sans-serif;
    font-weight: 700;
    color: var(--ink);
    white-space: nowrap;
  }
  .web-address {
    position: absolute;
    left: 0;
    width: 100%;
    bottom: 30px;
    text-align: center;
    font-family: "Source Sans 3", Arial, sans-serif;
    font-size: 19px;
    color: var(--text-grey);
  }
  .card--red .web-address { color: #ffffff; }

  /* front */
  .side-band {
    position: absolute; left: 0; top: 0;
    width: 62px; height: 100%;
    background: var(--brand-red);
  }
  .side-rule {
    position: absolute; left: 65px; top: 0;
    width: 3px; height: 100%;
    background: var(--ink);
  }
  .tint-square {
    position: absolute; left: 359px; top: 134px;
    width: 158px; height: 158px;
    background: var(--tint);
  }
  .front-brand {
    position: absolute; left: 107px; top: 64px;
    font-weight: 700; font-size: 58px; color: var(--ink);
  }
  .contact-name {
    position: absolute; left: 117px; top: 184px;
    font-size: 18px; font-weight: 700; color: var(--brand-red);
  }
  .contact-list {
    position: absolute; left: 117px; top: 214px;
    margin: 0; padding: 0; list-style: none;
    font-size: 14px; color: var(--text-grey);
  }
  .contact-list li { height: 26px; }
  .contact-list b { color: var(--ink); }

  .inset-panel {
    position: absolute; left: 81px; top: 82px;
    width: 362px; height: 128px;
    background: #ffffff;
    border: 1px solid #d6d6d6;
  }
</style>
</head>
<body>
<main class="sheet">
  <div class="side-label" style="left:53px;top:34px;">Front</div>
  <div class="side-label" style="left:622px;top:34px;">Back - 1</div>
  <div class="side-label" style="left:53px;top:404px;">Back - 2</div>
  <div class="side-label" style="left:622px;top:404px;">Back - 3</div>

  <section class="card card--front" style="left:53px;top:74px;">
    <div class="side-band"></div>
    <div class="side-rule"></div>
    <div class="tint-square"></div>
    <div class="front-brand">LorvanTest</div>
    <div class="contact-name">Todd Merrick</div>
    <ul class="contact-list">
      <li><b>p :</b> 877-514-9073 ext. 318</li>
      <li><b>e :</b> Todd@lorvantest.com</li>
      <li><b>w :</b> www.LorvanTest.com</li>
    </ul>
  </section>

  <section class="card card--white" style="left:622px;top:74px;">
    <div class="brand-name" style="top:88px;font-size:64px;">LorvanTest</div>
    <div class="web-address">www.LorvanTest.com</div>
  </section>

  <section class="card card--red" style="left:53px;top:445px;">
    <div class="brand-name" style="top:88px;font-size:64px;">LorvanTest</div>
    <div class="web-address">www.LorvanTest.com</div>
  </section>

  <section class="card card--grey" style="left:622px;top:445px;">
    <div class="inset-panel"></div>
    <div class="brand-name" style="top:118px;font-size:46px;">LorvanTest</div>
    <div class="web-address">www.LorvanTest.com</div>
  </section>
</main>
</body>
</html>
```